Heater product information sheets

I need the two product information sheets organized and laid out in a clean, easy to read attractive manner. These sheets are to advertise propane heaters for outdoor use and for wholesale to propane distributors, restaurants and homeowners that need to have propane heat as the winter ends and spring begins. They will be used for chilly evenings when people want to be outside eating, drinking and being social.

Target Market(s)

Restaurants, hospitality industry, special events, party rental companies, home owners with backyards

Font styles to use
Sans Serif

Requirements
Must have
• My logo in the document instead of t. Marlow and company
Nice to have
• I would like to see Fire illustrated coming up the heaters and on the round glass, show it up the middle of the glass tube propane heater.

```html
<!DOCTYPE html>
<html lang="en">
<head>
<meta charset="utf-8">
<title>Outdoor Propane Heater – Product Sheet</title>
<link href="https://fonts.googleapis.com/css2?family=Signika:wght@300;400;600;700&display=swap" rel="stylesheet">
<style>
  :root{
    --paper:#dcdcdc;
    --red:#d65a56;
    --slate:#454b5a;
    --ink:#2f3340;
    --amber:#e5b469;
    --tan:#dfc39c;
    --teal:#6ea09b;
    --hairline:#e2c38f;
  }
  *{margin:0;padding:0;box-sizing:border-box}
  html,body{width:848px;height:1200px;overflow:hidden;background:var(--paper)}
  body{font-family:"Signika",sans-serif;color:var(--ink)}
  .sheet{position:relative;width:848px;height:1200px;overflow:hidden;background:var(--paper)}
  .decor{position:absolute;inset:0}
  .abs{position:absolute;white-space:nowrap}
  .title-main{left:102px;top:62px;font-size:76px;font-weight:700;color:var(--red);line-height:1;letter-spacing:-1px}
  .title-sub{left:103px;top:151px;font-size:40px;font-weight:600;color:var(--slate);line-height:1;letter-spacing:-.5px}
  .product-photo{position:absolute;left:92px;top:230px;width:180px;height:485px}
  .section-head{font-size:28px;font-weight:700;color:var(--red);line-height:1;letter-spacing:-.3px}
  .spec{position:absolute;top:294px;width:130px;margin-left:-65px;text-align:center}
  .spec svg{display:block;margin:0 auto 10px;width:42px;height:40px}
  .spec p{font-size:13.5px;font-weight:300;line-height:17px;color:var(--ink)}
  .details{position:absolute;left:375px;top:462px;list-style:none;width:400px}
  .details li,.notes li{position:relative;font-size:21px;font-weight:300;line-height:23px;color:var(--ink)}
  .details li{padding-left:17px;margin-bottom:10px}
  .details li::before,.notes li::before{content:"";position:absolute;left:0;top:8px;width:10px;height:10px;border-radius:50%;background:var(--amber)}
  .details .justify{display:flex;justify-content:space-between;width:374px}
  .use{position:absolute;top:748px;width:110px;margin-left:-55px;text-align:center}
  .use svg{display:block;margin:0 auto 18px;width:56px;height:56px}
  .use p{font-size:11px;line-height:13.5px;text-transform:uppercase;color:var(--ink)}
  .notes{position:absolute;left:70px;top:925px;list-style:none}
  .notes li{padding-left:30px;margin-bottom:6px}
  .price{font-weight:700;color:var(--red);font-size:24px}
  .company{left:73px;top:1063px;font-size:21px;font-weight:300}
  .contact{position:absolute;display:flex;align-items:center;font-size:21px;font-weight:300}
  .contact .badge{width:25px;height:25px;border-radius:50%;background:var(--teal);display:flex;align-items:center;justify-content:center;margin-right:11px}
</style>
</head>
<body>
<main class="sheet">
  <svg class="decor" width="848" height="1200" viewBox="0 0 848 1200" aria-hidden="true">
    <circle cx="145" cy="182" r="129" fill="var(--amber)"/>
    <circle cx="-16" cy="575" r="92" fill="var(--tan)"/>
    <circle cx="858" cy="1218" r="140" fill="var(--tan)"/>
    <circle cx="653" cy="643" r="321" fill="none" stroke="var(--hairline)" stroke-width="0.8"/>
    <path d="M0 876 C120 900 235 1000 255 1200" fill="none" stroke="var(--hairline)" stroke-width="0.8"/>
  </svg>

  <h1 class="abs title-main">Outdoor</h1>
  <h2 class="abs title-sub">Propane Heater</h2>

  <svg class="product-photo" viewBox="0 0 180 485" role="img" aria-label="Photo of a black outdoor patio propane heater with glowing burner head">
    <defs>
      <linearGradient id="heaterTone" x1="0" y1="0" x2="0" y2="1">
        <stop offset="0" stop-color="#e8b45a"/>
        <stop offset=".2" stop-color="#8a8a8a"/>
        <stop offset=".45" stop-color="#3a3a3e"/>
        <stop offset="1" stop-color="#1d1d20"/>
      </linearGradient>
    </defs>
    <rect x="0" y="0" width="180" height="485" rx="20" fill="url(#heaterTone)" opacity=".85"/>
  </svg>

  <h3 class="abs section-head" style="left:339px;top:249px">SPECIFICATIONS</h3>

  <div class="spec" style="left:368px">
    <svg viewBox="0 0 42 40" fill="none" stroke="var(--teal)" stroke-width="1.6" stroke-linecap="round" stroke-linejoin="round"><path d="M24 6 L15 22 H22 L18 34 L28 17 H21 Z"/><path d="M21 1v3M21 36v3M3 20h4M35 20h4M8 8l3 3M31 29l3 3M34 8l-3 3M11 29l-3 3"/></svg>
    <p>Powerful<br>48,000 BTU</p>
  </div>
  <div class="spec" style="left:482px">
    <svg viewBox="0 0 42 40" fill="none" stroke="var(--teal)" stroke-width="1.6" stroke-linejoin="round"><path d="M3 4h36v6l-3 26H6L3 10z"/><path d="M3 10h36M9 14c2 6 4 6 6 0s4-6 6 0 4 6 6 0 4-6 6 0"/><path d="M8 32h26"/></svg>
    <p>Black Powder<br>Coated Finish</p>
  </div>
  <div class="spec" style="left:610px">
    <svg viewBox="0 0 42 40" fill="none" stroke="var(--teal)" stroke-width="1.6" stroke-linejoin="round"><rect x="17" y="1" width="8" height="5"/><path d="M14 6h14v4H14z"/><rect x="12" y="10" width="18" height="26" rx="5"/><path d="M12 20h18M12 26h18M16 36v3M26 36v3"/></svg>
    <p>Uses 20 lbs.<br>Propane Tank</p>
  </div>
  <div class="spec" style="left:739px">
    <svg viewBox="0 0 42 40" fill="none" stroke="var(--teal)" stroke-width="1.6" stroke-linejoin="round"><path d="M11 4h26v28H11z"/><path d="M4 32h30v5H4z"/><path d="M24 8l6 2v5c0 4-3 6-6 7-3-1-6-3-6-7v-5z"/><path d="M16 26h16"/></svg>
    <p>CE, GS, AGA, CSA,<br>with ETL certificate<br>and ROHS approved.</p>
  </div>

  <h3 class="abs section-head" style="left:340px;top:411px">ADDITIONAL DETAILS</h3>

  <ul class="details">
    <li>Commercial Quality</li>
    <li>For Outdoor Use Only</li>
    <li><span class="justify"><span>Conforms</span><span>to</span><span>ANSI</span><span>STD</span><span>Z83.26-2014</span></span></li>
    <li>Certified to CSA STD 2.37-2014 Gas- fired outdoor infrared patio heaters</li>
    <li>Safety Auto Shut Off Switch</li>
    <li>Thermostatic Control</li>
    <li>Base Diameter 17” - Anti-Tip Design</li>
    <li>Standard Wheels - Tilt &amp; Move</li>
    <li>Run time: 8-10 hours with standard 20 lbs. Propane tank</li>
    <li>88” Tall</li>
    <li>Heating Area: 200 sq. ft</li>
  </ul>

  <div class="use" style="left:77px">
    <svg viewBox="0 0 56 56" fill="none" stroke="var(--teal)" stroke-width="1.6" stroke-linejoin="round"><path d="M2 8 Q28 14 52 4"/><path d="M4 9l3 7 4-6 4 7 3-6 5 6 3-7 5 6 3-7 5 5 3-8"/><path d="M14 26 Q34 30 54 22"/><path d="M16 27l3 6 4-5 4 6 3-6 5 6 3-6 5 5 3-7"/><path d="M2 40 Q22 44 42 36"/><path d="M4 41l3 7 4-6 4 7 3-6 5 6 3-7 5 5 2-7"/></svg>
    <p>Rentals for<br>live events</p>
  </div>
  <div class="use" style="left:188px">
    <svg viewBox="0 0 56 56" fill="none" stroke="var(--teal)" stroke-width="1.6" stroke-linejoin="round"><circle cx="28" cy="5" r="2.5"/><path d="M8 30a20 20 0 0 1 40 0z"/><path d="M4 30h48v4H4z"/><path d="M14 20a15 15 0 0 1 8-8"/><path d="M6 40h26l14-6"/><path d="M2 38v14M2 48h24l18-6"/></svg>
    <p>Rentals for<br>restaurants &amp;<br>catering halls</p>
  </div>
  <div class="use" style="left:295px">
    <svg viewBox="0 0 56 56" fill="none" stroke="var(--teal)" stroke-width="1.6" stroke-linejoin="round"><path d="M3 26L28 5l25 21"/><path d="M40 14V4h5v14"/><path d="M9 22v30h38V22"/><rect x="15" y="30" width="11" height="10"/><path d="M20.5 30v10M15 35h11"/><path d="M31 52V30h10v22"/><path d="M2 52h52"/></svg>
    <p>Purchase for<br>your home or<br>business</p>
  </div>

  <h3 class="abs section-head" style="left:68px;top:892px">NOTE:</h3>
  <ul class="notes">
    <li>Price: Starting at <span class="price">$250</span> each</li>
    <li>Assembly &amp; Delivery available upon request</li>
    <li>Discounts for large quantity orders</li>
  </ul>

  <h3 class="abs section-head" style="left:72px;top:1027px">To Rent or Purchase:</h3>
  <p class="abs company">T. Marlow &amp; Company</p>

  <div class="contact" style="left:72px;top:1097px">
    <span class="badge"><svg width="13" height="13" viewBox="0 0 24 24" fill="#fff"><path d="M6.6 10.8a15 15 0 0 0 6.6 6.6l2.2-2.2c.3-.3.7-.4 1-.2 1.1.4 2.3.6 3.6.6.6 0 1 .4 1 1V20c0 .6-.4 1-1 1A17 17 0 0 1 3 4c0-.6.4-1 1-1h3.5c.6 0 1 .4 1 1 0 1.3.2 2.5.6 3.6.1.3 0 .7-.2 1z"/></svg></span>555-410-2286
  </div>
  <div class="contact" style="left:296px;top:1097px">
    <span class="badge"><svg width="13" height="13" viewBox="0 0 24 24" fill="none" stroke="#fff" stroke-width="2"><rect x="3" y="5" width="18" height="14" rx="1"/><path d="M3 6l9 7 9-7"/></svg></span>Dana@TMeventrental.com
  </div>
  <div class="contact" style="left:72px;top:1135px">
    <span class="badge"><svg width="13" height="13" viewBox="0 0 24 24" fill="none" stroke="#fff" stroke-width="2"><path d="M12 22s7-7 7-12a7 7 0 0 0-14 0c0 5 7 12 7 12z"/><circle cx="12" cy="10" r="2.5"/></svg></span>42 Foundry Lane Millbrook, NJ 07099
  </div>
</main>
</body>
</html>
```